Shipping and Logistics, Project

Project description : Company Profile

A total logistics company covering domestic / international freight forwarding, warehouse management services, haulage, supply chain management, transport management & distribution, procurement & assembly services, shipping, chartering & bunker services, project logistics & tax exemption consultancy, oil & gas logistics, halal logistics services & integrated logistics management. We’re a well-established and experienced freight forwarder in Kuala Lumpur, Malaysia. We specialize in customized value-added solution that optimizes your supply chain by trimming inventory, reducing logistics cost and enhancing your customer service levels.

As a member of the Worldwide Parcel and Carriage Alliance which comprise of 170 global freight agents in 80 countries that promotes great handling in cross-trade logistics and freighting. You could rely on our efficiency in handlings of export cargo (FCL, LCL, Bulk and Conventional) between our global network offices worldwide with a total scale of 10,000 groomed specialists in various logistics division working together to ensure delivery task meets with your expectation. With our dedicated qualified and experienced professionals, we are fully committed to serving our clients.

Our generic services are listed below for your reference:

• Air Freight
• Ocean Freight FCL & LCL
• Container Haulage
• Warehousing
• Transportation and Distribution within Malaysia and Thailand
• Cross-Border Road Line-hauls between Thailand, Malaysia, Singapore and Laos
• Customs Brokerage and Forwarding
• Project Cargo Freight Forwarding for setting up of new plants / factories and ad hoc heavy-lift
• Air-Sea-Road-Rail multi-modal options
• Import / Export / Storage / Documentation / Handling of DG / Hazmat
• Vessel and Aircraft Charters

Our Mission
Based on the motto “Quick, Reliable and Polite”, we are dedicated to upholding the following three points corporate philosophy:
1. Adhering to the principle that “the customer always comes first”.
2. Contributing to the development of the local community.
3. Making it our duty to be responsible and sincere.

Our Edge
• One-Stop Logistics Solutions
• Extensive Network Throughout Malaysia
• Highly Qualified and Experienced Pool of Professionals
• Comprehensive IT Solutions
• Innovative and Customer-focused Solutions
• Flexible and Consistent in Managing Exceptions
• Total Supply Chain Visibility

Target Market
1. We sell the logistics services to all the industry in Malaysia and Worldwide. (ONE Stop Logistics Solutions)

Competitor
1. TR Valmont
2. Corvessa Transport
3. Brandt + Loewe
4. FELRO
5. QTV
6. Routemarks
7. Ilto Logistics

Rules for Picking a Company Name
1. Unique and unforgettable
2. Avoid unusual spellings
3. Easy to pronounce and remember
4. Keep it simple
5. Make some sense
6. Give a clue

Rules for Picking a Company Logo
4. Keep it simple
5. Make some sense
6. Give a clue

1. Simplicity
2. Memorability
3. Originality
4. Modern Yet Timeless
5. Balance
6. Complementary
7. Versatility

Stationery Information
1. Company Name : ZENFreight Solutions Sdn Bhd
2. Company Registration : 2837165-W
3. Address : 42-08, Jalan Cempaka Indah 5, Taman Seri Bayu, 81300 Johor Bahru, Johor, Malaysia.
4. Name : Derek Tan
5. Position : Manager
6. Mobile No : (+6019) 4381907
7. Office No : (+607) 5218764
8. Fax No : Not Available
9. Email Address : derek.tan@zenfreight-solutions.example
10. Web Domain : www.zenfreight-solutions.example
11. Company Slogan : Be Globally Connected

Target Market(s)

Corporate Company

Industry/Entity Type

Shipping and Logistics Industry

Requirements
Must have
• Company Full Name : ZENFREIGHT SOLUTIONS SDN. BHD.
Nice to have
• Keep it simple and unforgettable ...

```html
<!DOCTYPE html>
<html lang="en">
<head>
<meta charset="utf-8">
<title>ZENFreight Solutions Stationery</title>
<link href="https://fonts.googleapis.com/css2?family=Poppins:wght@400;500&display=swap" rel="stylesheet">
<style>
:root{
  --stage:#c8c8c8;
  --ink:#2a2a2a;
  --folder:#282828;
  --blue:#3b88c9;
  --paper:#ffffff;
  --rule:#cfcfcf;
  --text-dark:#1e1e1e;
}
*{margin:0;padding:0;box-sizing:border-box}
html,body{width:1200px;height:900px;overflow:hidden}
body{background:var(--stage);font-family:"Poppins",sans-serif;position:relative;color:var(--text-dark)}
.piece{position:absolute}
.brand{position:absolute;display:flex;align-items:center}
.brand-mark{border:2px solid var(--blue);flex:none}
.brand-words{margin-left:6px;line-height:1}
.brand-name{font-weight:500;color:var(--blue);display:block;letter-spacing:.02em}
.brand-sub{display:block;letter-spacing:.18em;margin-top:2px}

/* folder */
.folder{left:114px;top:145px;width:314px;height:436px;background:var(--folder)}
.folder .brand{left:104px;top:32px}
.folder .brand-mark{width:40px;height:40px;border-width:3px}
.folder .brand-words{margin-left:10px}
.folder .brand-name{font-size:22px}
.folder .brand-sub{font-size:8.5px;color:#fff;margin-top:6px;letter-spacing:.22em}
.folder-slogan{position:absolute;left:0;right:0;top:400px;text-align:center;color:#fff;font-size:9px;letter-spacing:.18em}

/* letterhead */
.letterhead{left:460px;top:154px;width:291px;height:425px;background:var(--paper)}
.letterhead .brand{left:24px;top:12px}
.small-brand .brand-mark{width:22px;height:22px}
.small-brand .brand-name{font-size:11px}
.small-brand .brand-sub{font-size:4.2px;color:var(--text-dark)}
.contact{position:absolute;right:19px;top:14px;text-align:right;font-size:5px;line-height:1.25}
.contact .link{color:var(--blue)}
.contact .address{margin-top:5px}
.header-rule{position:absolute;left:19px;top:52px;width:184px;height:1px;background:var(--rule)}

/* footer band */
.footer-band{position:absolute;left:0;right:0;bottom:0;height:20px}
.footer-band svg{position:absolute;inset:0}
.footer-band span{position:absolute;top:5px;font-size:6px;color:#fff}

/* tall envelope */
.envelope-tall{left:786px;top:94px;width:307px;height:488px}
.envelope-tall .flap,.envelope-wide .flap{position:absolute;left:0;top:0}
.envelope-tall .body{position:absolute;left:0;top:58px;width:307px;height:430px;background:var(--paper)}
.envelope-tall .brand{left:25px;top:36px}
.envelope-tall .address{position:absolute;left:0;right:0;top:381px;text-align:center;font-size:6px;line-height:1.2}

/* wide envelope */
.envelope-wide{left:436px;top:624px;width:340px;height:196px}
.envelope-wide .body{position:absolute;left:0;top:26px;width:340px;height:170px;background:var(--paper)}
.envelope-wide .brand{left:17px;top:23px}
.envelope-wide .address{position:absolute;left:19px;top:140px;font-size:5.5px;line-height:1.2}
</style>
</head>
<body>

<section class="piece folder" aria-label="Presentation folder">
  <div class="brand">
    <span class="brand-mark"></span>
    <span class="brand-words">
      <span class="brand-name">ZENFREIGHT</span>
      <span class="brand-sub">SOLUTIONS SDN. BHD.</span>
    </span>
  </div>
  <p class="folder-slogan">BE GLOBALLY CONNECTED</p>
</section>

<section class="piece letterhead" aria-label="Letterhead">
  <div class="brand small-brand">
    <span class="brand-mark"></span>
    <span class="brand-words">
      <span class="brand-name">ZENFREIGHT</span>
      <span class="brand-sub">SOLUTIONS SDN. BHD.</span>
    </span>
  </div>
  <div class="contact">
    <p>(+6019) 438 1907, (+607) 521 8764</p>
    <p>derek.tan@zenfreight-solutions.example</p>
    <p>www.<span class="link">zenfreight-solutions</span>.example</p>
    <p class="address">42-08, Jalan Cempaka Indah 5,<br>Taman Seri Bayu, 81300 Johor<br>Bahru, Johor, Malaysia.</p>
  </div>
  <div class="header-rule"></div>
  <div class="footer-band">
    <svg width="291" height="20" viewBox="0 0 291 20">
      <polygon points="0,18 291,18 291,20 0,20" fill="var(--blue)"/>
      <polygon points="136,0 291,0 291,18 126,18" fill="var(--blue)"/>
      <polygon points="0,0 134,0 124,16 0,16" fill="var(--ink)"/>
    </svg>
    <span style="left:31px">Company No. 2837165-W</span>
    <span style="left:171px">BE GLOBALLY CONNECTED</span>
  </div>
</section>

<section class="piece envelope-tall" aria-label="Large envelope">
  <svg class="flap" width="307" height="60" viewBox="0 0 307 60">
    <polygon points="32,0 269,0 307,52 307,60 0,57 0,54" fill="var(--blue)"/>
  </svg>
  <div class="body">
    <div class="brand small-brand">
      <span class="brand-mark"></span>
      <span class="brand-words">
        <span class="brand-name">ZENFREIGHT</span>
        <span class="brand-sub">SOLUTIONS SDN. BHD.</span>
      </span>
    </div>
    <p class="address">42-08, Jalan Cempaka Indah 5,<br>Taman Seri Bayu, 81300 Johor<br>Bahru, Johor, Malaysia.</p>
    <div class="footer-band">
      <svg width="307" height="20" viewBox="0 0 307 20">
        <polygon points="0,18 307,18 307,20 0,20" fill="var(--blue)"/>
        <polygon points="142,0 307,0 307,18 132,18" fill="var(--blue)"/>
        <polygon points="0,0 140,0 130,16 0,16" fill="var(--ink)"/>
      </svg>
      <span style="left:42px">Company No. 2837165-W</span>
      <span style="left:174px">BE GLOBALLY CONNECTED</span>
    </div>
  </div>
</section>

<section class="piece envelope-wide" aria-label="DL envelope">
  <svg class="flap" width="340" height="27" viewBox="0 0 340 27">
    <polygon points="15,0 322,0 340,26 0,26" fill="var(--blue)"/>
  </svg>
  <div class="body">
    <div class="brand small-brand">
      <span class="brand-mark"></span>
      <span class="brand-words">
        <span class="brand-name">ZENFREIGHT</span>
        <span class="brand-sub">SOLUTIONS SDN. BHD.</span>
      </span>
    </div>
    <p class="address">42-08, Jalan Cempaka Indah 5,<br>Taman Seri Bayu, 81300 Johor<br>Bahru, Johor, Malaysia.</p>
  </div>
</section>

</body>
</html>
```